BrivoTerna. Lantern of the Steady Harvest. Business card

Professional business card for BrivoTerna (Lantern of the Steady Harvest)
My rationale: Strategy-> Execution-> Results-> Value that lead to the BrivoTerna name: We put the Lantern of the Steady Harvest.
We deliver value to our customers helping them at defining a good strategy (cyan arrow). 90% of well formulated strategies fail due to poor execution so we also consider strategical execution very important (green arrow). Due to the execution we obtain the results (blue arrow). Finally, the results provide feedback to redefine strategy, and the new strategy has to be executed and new results obtained providing new feedback and on and on. It's like a wheel that finally, must create corporate value: value for shareholders, staholders, employees, providers...-

Target Market(s)

CEOs and steering comitees , invewrnent funds

Industry/Entity Type

Business Consultant

Contact Information for Business Card

Teodoro Vinsquel
CEO & Founder
teodoro.vinsquel@brivoterna-example.com
Mobile: +34 655.803.912
www.brivoterna-example.com

Colors

Designer to choose colors to be used in the design.

Requirements
Nice to have
• Nice to hace the words: Strategy, execution, results
• Nice to vave the claim: Lantern of the Steady Harvest
• The three colors should be shown:
• cyan for STRATEGY
• green for EXECUTION
• blue for RESULTS
Should not have
• Complete black background

```html
<!DOCTYPE html>
<html lang="en">
<head>
<meta charset="utf-8">
<title>BrivoTerna – Business Card</title>
<link rel="stylesheet" href="https://fonts.googleapis.com/css2?family=Fira+Sans:wght@400;600;700&family=Arimo:wght@400;700&display=swap">
<style>
  :root {
    --page-bg: #e6e9ef;
    --brand-blue: #0a33a0;
    --brand-navy: #0b2f95;
    --strategy-cyan: #08aeea;
    --strategy-cyan-dark: #0a86d6;
    --execution-green: #8cc63f;
    --card-white: #ffffff;
    --text-white: #ffffff;
    --card-shadow: 0 18px 40px rgba(20, 30, 60, 0.22);
  }
  * { box-sizing: border-box; margin: 0; padding: 0; }
  html, body {
    width: 1200px;
    height: 960px;
    overflow: hidden;
    background: var(--page-bg);
    font-family: "Fira Sans", Arial, sans-serif;
  }
  .sheet {
    position: relative;
    width: 1200px;
    height: 960px;
    display: flex;
    flex-direction: column;
    align-items: center;
    justify-content: center;
    gap: 60px;
  }
  .card {
    position: relative;
    width: 720px;
    height: 400px;
    overflow: hidden;
    box-shadow: var(--card-shadow);
  }

  /* Back of card */
  .card-back {
    background: var(--brand-blue);
    display: flex;
    flex-direction: column;
    align-items: center;
    justify-content: center;
  }
  .brand-lockup {
    display: flex;
    align-items: center;
    gap: 16px;
  }
  .brand-dot {
    width: 22px;
    height: 22px;
    border-radius: 50%;
    background: var(--text-white);
  }
  .brand-name {
    font-family: "Fira Sans", Arial, sans-serif;
    font-weight: 700;
    font-size: 66px;
    letter-spacing: -1px;
    color: var(--text-white);
    line-height: 1;
  }
  .back-url {
    margin-top: 34px;
    font-size: 17px;
    letter-spacing: 3.5px;
    color: var(--text-white);
  }

  /* Front of card */
  .card-front { background: var(--card-white); }
  .front-shapes {
    position: absolute;
    inset: 0;
    width: 720px;
    height: 400px;
  }
  .front-brand {
    position: absolute;
    left: 48px;
    top: 150px;
    display: flex;
    align-items: center;
    gap: 12px;
  }
  .front-brand .brand-dot {
    width: 18px;
    height: 18px;
    background: var(--brand-navy);
  }
  .front-brand .brand-name {
    font-size: 50px;
    color: var(--brand-navy);
  }
  .holder {
    position: absolute;
    right: 26px;
    top: 140px;
    text-align: right;
    font-family: "Arimo", Arial, sans-serif;
    color: var(--text-white);
  }
  .holder-name {
    font-weight: 700;
    font-size: 24px;
    line-height: 1.1;
  }
  .holder-role {
    font-size: 16px;
    margin-top: 3px;
  }
  .contacts {
    position: absolute;
    right: 26px;
    top: 232px;
    list-style: none;
    font-family: "Fira Sans", Arial, sans-serif;
    font-size: 15px;
    color: var(--text-white);
  }
  .contacts li {
    display: flex;
    justify-content: flex-end;
    align-items: center;
    gap: 10px;
    height: 27px;
  }
  .contacts svg {
    width: 16px;
    height: 16px;
    flex: none;
  }
  .tagline {
    position: absolute;
    right: 26px;
    bottom: 34px;
    font-weight: 700;
    font-size: 20px;
    color: var(--execution-green);
    word-spacing: 2px;
  }
</style>
</head>
<body>
<main class="sheet">

  <section class="card card-back" aria-label="Business card, back">
    <div class="brand-lockup">
      <span class="brand-dot"></span>
      <span class="brand-name">BrivoTerna</span>
    </div>
    <p class="back-url">www.brivoterna-example.com</p>
  </section>

  <section class="card card-front" aria-label="Business card, front">
    <svg class="front-shapes" viewBox="0 0 720 400" aria-hidden="true">
      <polygon points="470,0 720,0 720,400 250,400" fill="var(--brand-blue)"/>
      <polygon points="340,195 384,195 384,242" fill="var(--strategy-cyan-dark)"/>
      <rect x="340" y="135" width="380" height="60" fill="var(--strategy-cyan)"/>
    </svg>

    <div class="front-brand">
      <span class="brand-dot"></span>
      <span class="brand-name">BrivoTerna</span>
    </div>

    <div class="holder">
      <p class="holder-name">Teodoro Vinsquel</p>
      <p class="holder-role">CEO &amp; Founder</p>
    </div>

    <ul class="contacts">
      <li>+34 655.803.912
        <svg viewBox="0 0 16 16" aria-label="Mobile"><rect x="4" y="1" width="8" height="14" rx="1.5" fill="none" stroke="var(--text-white)" stroke-width="1.4"/><line x1="7" y1="12.5" x2="9" y2="12.5" stroke="var(--text-white)" stroke-width="1.4"/></svg>
      </li>
      <li>www.brivoterna-example.com
        <svg viewBox="0 0 16 16" aria-label="Website"><circle cx="8" cy="8" r="6.5" fill="none" stroke="var(--text-white)" stroke-width="1.3"/><ellipse cx="8" cy="8" rx="3" ry="6.5" fill="none" stroke="var(--text-white)" stroke-width="1.1"/><line x1="1.5" y1="8" x2="14.5" y2="8" stroke="var(--text-white)" stroke-width="1.1"/></svg>
      </li>
      <li>teodoro.vinsquel@brivoterna-example.com
        <svg viewBox="0 0 16 16" aria-label="Email"><rect x="1.5" y="3.5" width="13" height="9" fill="none" stroke="var(--text-white)" stroke-width="1.3"/><polyline points="1.5,3.5 8,9 14.5,3.5" fill="none" stroke="var(--text-white)" stroke-width="1.3"/></svg>
      </li>
    </ul>

    <p class="tagline">Strategy • Execution • Results</p>
  </section>

</main>
</body>
</html>
```